Design and Renovation Company Luxury Business Card

I want to create a luxury business card for a Design and Renovation Firm . We will use our current logo. The company name is 528BUILDA. We do not want anything standard. We need a very unique concept.
Please see uploaded inspiration. I really like the textured paper option. I would like the card to be thick with debossing, and/or embossing options. The logo has orange in it but I would like to see the card with and without the orange. I think the orange may make the company feel less high-end. The goal is to elevate the logo not match its vibe per se of the logo. We want something very unique, not standard at all!
I would like a space for :
Logo,
Name,
Position,
Email,
Office number,
Website Address,
Business Address,
Thank you!
Have fun!
Target Market(s)
Home owners Age 35 +
Industry/Entity Type
Design and Renovation
Contact Information for Business Card
Logo, Name, Position, Email, Office number, Website Address, Business Address,.
Colors
Designer to choose colors to be used in the design.
Requirements
Must have
- A luxury designer feel. Must be black or dark grey but open to other luxury ideas.
Nice to have
- Gold, silver, black embossing or debossing. Textured paper design.
Should not have
- A cheap look and feel.

```html
<!DOCTYPE html>
<html lang="en">
<head>
<meta charset="utf-8">
<title>528BUILDA Business Card</title>
<link rel="stylesheet" href="https://fonts.googleapis.com/css2?family=Ubuntu:wght@400;500;700&display=swap">
<style>
  :root {
    --backdrop: #d3d6d6;
    --card-black: #1b1b1c;
    --card-black-soft: #242425;
    --foil-silver: #e4e4e4;
    --accent-orange: #e0761d;
    --edge-orange: #d9661a;
    --text-light: #ededed;
  }
  * { box-sizing: border-box; margin: 0; padding: 0; }
  html, body {
    width: 1200px;
    height: 1050px;
    overflow: hidden;
    background: var(--backdrop);
    font-family: "Ubuntu", sans-serif;
  }
  .canvas {
    position: relative;
    width: 1200px;
    height: 1050px;
  }
  .card {
    position: absolute;
    left: 250px;
    width: 700px;
    height: 400px;
    border-radius: 3px;
    background: radial-gradient(circle at 30% 25%, var(--card-black-soft), var(--card-black) 70%);
    border-bottom: 5px solid var(--edge-orange);
    box-shadow: 0 14px 28px rgba(0, 0, 0, 0.22);
    overflow: hidden;
  }
  .card--logo { top: 80px; }
  .card--contact { top: 560px; }

  /* Company name and tagline, set as plain text */
  .company {
    position: absolute;
    display: flex;
    flex-direction: column;
    align-items: flex-start;
  }
  .company__name {
    font-weight: 400;
    color: var(--foil-silver);
    line-height: 1;
  }
  .company__tagline {
    font-weight: 400;
    color: var(--foil-silver);
  }

  .card--logo .company {
    left: 0;
    right: 0;
    top: 150px;
    align-items: center;
  }
  .card--logo .company__name { font-size: 68px; }
  .card--logo .company__tagline { font-size: 18px; margin-top: 16px; }

  .card--contact .company {
    left: 48px;
    top: 160px;
  }
  .card--contact .company__name { font-size: 32px; }
  .card--contact .company__tagline { font-size: 11px; margin-top: 8px; }

  .divider {
    position: absolute;
    left: 352px;
    top: 70px;
    width: 2px;
    height: 250px;
    background: var(--accent-orange);
  }

  .contact {
    position: absolute;
    left: 384px;
    top: 72px;
    color: var(--text-light);
  }
  .contact__name {
    color: var(--accent-orange);
    font-weight: 700;
    font-size: 26px;
    letter-spacing: 0.02em;
  }
  .contact__role {
    font-size: 16px;
    margin-top: 4px;
  }
  .contact__address {
    font-size: 15px;
    line-height: 1.35;
    margin-top: 22px;
  }
  .contact__list {
    list-style: none;
    margin-top: 22px;
    font-size: 15px;
  }
  .contact__item {
    display: flex;
    align-items: center;
    gap: 10px;
    margin-bottom: 6px;
  }
  .contact__icon {
    width: 14px;
    height: 14px;
    flex: none;
    fill: var(--accent-orange);
  }
</style>
</head>
<body>
<main class="canvas">

  <section class="card card--logo" aria-label="Card back">
    <div class="company">
      <span class="company__name">528BUILDA</span>
      <span class="company__tagline">Design and Renovation Firm</span>
    </div>
  </section>

  <section class="card card--contact" aria-label="Card front">
    <div class="company">
      <span class="company__name">528BUILDA</span>
      <span class="company__tagline">Design and Renovation Firm</span>
    </div>

    <div class="divider"></div>

    <div class="contact">
      <p class="contact__name">DANIEL REYES</p>
      <p class="contact__role">Medical Director</p>
      <p class="contact__address">418 Harbor View Lane Suite<br>12 Westbury, New York 11590</p>
      <ul class="contact__list">
        <li class="contact__item">
          <svg class="contact__icon" viewBox="0 0 24 24" aria-hidden="true"><path d="M6.6 10.8a15.1 15.1 0 0 0 6.6 6.6l2.2-2.2c.3-.3.7-.4 1-.2 1.1.4 2.3.6 3.6.6.6 0 1 .4 1 1V20c0 .6-.4 1-1 1A17 17 0 0 1 3 4c0-.6.4-1 1-1h3.5c.6 0 1 .4 1 1 0 1.3.2 2.5.6 3.6.1.3 0 .7-.2 1z"/></svg>
          <span>(555)214-7390</span>
        </li>
        <li class="contact__item">
          <svg class="contact__icon" viewBox="0 0 24 24" aria-hidden="true"><path d="M2 5h20v14H2z M2 5l10 8 10-8" fill="var(--accent-orange)" stroke="var(--card-black)" stroke-width="1.6"/></svg>
          <span>hello@528builda.com</span>
        </li>
        <li class="contact__item">
          <svg class="contact__icon" viewBox="0 0 24 24" aria-hidden="true"><circle cx="12" cy="12" r="10"/><path d="M2 12h20M12 2c3 3 3 17 0 20M12 2c-3 3-3 17 0 20" fill="none" stroke="var(--card-black)" stroke-width="1.5"/></svg>
          <span>www.528builda.com</span>
        </li>
      </ul>
    </div>
  </section>

</main>
</body>
</html>
```